Supplement Bottle Label Design and Creative Lifestyle Images

We are a medical home consumer brand and we are releasing a supplement line of products called "Veltrix Wellness". We are in need of a supplement bottle design for our supplement line, Veltrix Wellness. We are looking for a very appealing, simple, and clean design, but with a medical feel to it.

We would like to see designs with a black background as well as designs with a white background. Bottle size will approximately be 200cc and label will about be 7" x 2.5", but this size is subject to change.

We really like the Brenna Nutrition design and the Field Kinetics, however, we like the medical style of Nutrition Cornerstone. Please reference the links below.

To start off, the title of this bottle will be "Mindalux". We will need all similar warning about HRB, made in USA, non-GMA, GMP, ect. Please use the formula below to start:

2 Pills per serving
Blueberry pterostilbene - 10mg
Bacopa - 150mg
Gingko Biloba - 50mg
Vinpocetine - 10mg
Alpha-GPC -150mg
TAU - 35mg

https://www.shopvarlo.example/Brenna-Nutrition/b/ref=bl_dp_s_web_48213906722?ie=UTF8&node=48213906722&field-lbr_brands_browse-bin=Brenna+Nutrition

https://www.shopvarlo.example/l/7394025188

https://www.shopvarlo.example/Nutrition-Cornerstone/b/ref=bl_dp_s_web_56071238493?ie=UTF8&node=56071238493&field-lbr_brands_browse-bin=Nutrition+Cornerstone

```html
<!DOCTYPE html>
<html lang="en">
<head>
<meta charset="utf-8">
<title>Mindalux – Veltrix Wellness Label</title>
<link rel="stylesheet" href="https://fonts.googleapis.com/css2?family=Encode+Sans+Condensed:wght@300;400;700&family=Teko:wght@400&display=swap">
<style>
  :root {
    --label-black: #0d0d0d;
    --brand-orange: #f29a1f;
    --title-grey: #b4b4b4;
    --title-orange: #f0592a;
    --tagline-orange: #f28a1e;
    --tagline-white: #f2f2f2;
    --volume-red: #e0542a;
    --dot-light: #a9a9a9;
    --dot-dark: #3a3a3a;
  }
  html, body {
    margin: 0;
    padding: 0;
    width: 1200px;
    height: 2171px;
    overflow: hidden;
    background: var(--label-black);
  }
  .label {
    position: relative;
    width: 1200px;
    height: 2171px;
    background: var(--label-black);
    font-family: "Encode Sans Condensed", "Arial Narrow", sans-serif;
  }
  .brand {
    position: absolute;
    top: 560px;
    left: 0;
    width: 1200px;
    display: flex;
    justify-content: center;
    align-items: center;
    gap: 22px;
  }
  .brand-dot {
    width: 62px;
    height: 62px;
    border-radius: 50%;
    background: var(--brand-orange);
  }
  .brand-name {
    font-weight: 700;
    font-size: 64px;
    color: var(--brand-orange);
    letter-spacing: 0.5px;
  }
  .molecule-graphic {
    position: absolute;
    top: 720px;
    left: 285px;
    width: 630px;
    height: 630px;
    border-radius: 50%;
    background: radial-gradient(circle, var(--dot-light) 0%, #6e6e6e 40%, var(--dot-dark) 70%, var(--label-black) 100%);
  }
  .product-title {
    position: absolute;
    top: 1365px;
    left: 0;
    width: 1200px;
    margin: 0;
    text-align: center;
    font-family: "Teko", "Arial Narrow", sans-serif;
    font-weight: 400;
    font-size: 300px;
    line-height: 1;
    letter-spacing: 12px;
    text-transform: uppercase;
  }
  .title-grey { color: var(--title-grey); }
  .title-orange { color: var(--title-orange); }
  .claims {
    position: absolute;
    top: 1650px;
    left: 0;
    width: 1200px;
    text-align: center;
    font-weight: 300;
    font-size: 40px;
    line-height: 64px;
    letter-spacing: -0.5px;
    text-transform: uppercase;
  }
  .claim { display: block; color: var(--tagline-orange); }
  .claim-type { color: var(--tagline-white); }
  .volume {
    position: absolute;
    top: 1870px;
    left: 0;
    width: 1200px;
    text-align: center;
    font-weight: 300;
    font-size: 40px;
    color: var(--volume-red);
  }
</style>
</head>
<body>
  <main class="label">
    <div class="brand">
      <span class="brand-dot"></span>
      <span class="brand-name">Veltrix Wellness</span>
    </div>
    <div class="molecule-graphic" role="img" aria-label="Radial cluster of grey molecular dots"></div>
    <h1 class="product-title"><span class="title-grey">Minda</span><span class="title-orange">lux</span></h1>
    <p class="claims">
      <span class="claim">For a better memory</span>
      <span class="claim">More focus &amp; clarity</span>
      <span class="claim claim-type">Dietary supplement</span>
    </p>
    <div class="volume">200cc</div>
  </main>
</body>
</html>
```